Home Remodeling company needs a business card design

we need a business card design for home remodeling company in hamilton county, indiana USA. we offers a wide range of construction services including whole house renovations, Design and Build Basements and Kitchen and Bathroom Remodeling . we would like to see designs for both site of business card that use the same color of the company logo and also including all information below :
1- Karim Feltous CEO / General Contractor
2- all company contacts Telephone numbers ( 1-888-DULOM-47 ) ( 317-555-0193) email address ( info@dulomhome.com) website ( www.dulomhome.com ) and social media logos (Facebook- twitter- google plus )
3- company logo
4- licensed . insured . bonded

```html
<!DOCTYPE html>
<html lang="en">
<head>
<meta charset="utf-8">
<title>Dulom Home Remodeling – Business Card</title>
<link rel="stylesheet" href="https://fonts.googleapis.com/css2?family=Cabin:ital,wght@0,400;0,500;0,600;0,700;1,400&display=swap">
<style>
  :root {
    --backdrop: #8e8f8f;
    --card-light: #f2f2f1;
    --card-dark: #333334;
    --ink: #2f2f30;
    --ink-soft: #3c3c3d;
    --brand-red: #b1232b;
    --rule: #9c9c9c;
    --white: #ffffff;
    --pale: #e9e9e9;
  }
  * { box-sizing: border-box; margin: 0; padding: 0; }
  html, body {
    width: 1105px; height: 1200px; overflow: hidden;
    background: var(--backdrop);
    font-family: "Cabin", "Gill Sans", sans-serif;
  }
  .canvas { position: relative; width: 1105px; height: 1200px; }

  .card {
    position: absolute; left: 180px; width: 745px; height: 425px; overflow: hidden;
  }
  .card-front { top: 119px; background: var(--card-light); }
  .card-back { top: 636px; background: var(--card-dark); }

  /* company name placeholder */
  .company-name {
    position: absolute; white-space: nowrap;
    font-weight: 700; font-size: 34px; line-height: 40px; color: var(--ink);
  }
  .card-front .company-name { right: 48px; top: 55px; }
  .card-back .company-name {
    left: 50%; top: 192px; transform: translateX(-50%); color: var(--pale);
  }

  /* person */
  .person { position: absolute; left: 44px; top: 199px; }
  .person-name {
    font-weight: 600; font-size: 26px; line-height: 30px; color: var(--ink); letter-spacing: .3px;
  }
  .person-role { font-size: 20px; line-height: 26px; margin-top: 2px; color: var(--brand-red); }
  .divider { position: absolute; left: 43px; right: 48px; top: 266px; height: 2px; background: var(--rule); }

  .contacts { position: absolute; left: 44px; top: 278px; list-style: none; }
  .contacts li {
    display: flex; align-items: center; gap: 10px; height: 28.5px;
    font-size: 19px; color: var(--ink-soft);
  }
  .contacts svg { width: 16px; height: 16px; fill: var(--ink); flex: none; }

  .credentials {
    position: absolute; right: 44px; top: 308px; text-align: right;
    font-size: 21px; line-height: 29px; color: var(--brand-red); letter-spacing: .3px;
  }

  .footer-band { position: absolute; left: 0; bottom: 0; width: 745px; height: 42px; }
  .website {
    position: absolute; right: 30px; bottom: 9px;
    font-style: italic; font-size: 18px; letter-spacing: 3.4px; color: var(--white);
  }

  .social { position: absolute; left: 50%; top: 361px; transform: translateX(-50%); }
</style>
</head>
<body>
<main class="canvas">

  <section class="card card-front" aria-label="Business card front">
    <p class="company-name">Dulom Home Remodeling</p>

    <div class="person">
      <h1 class="person-name">Karim Feltous</h1>
      <p class="person-role">CEO / General Contractor</p>
    </div>
    <div class="divider"></div>

    <ul class="contacts">
      <li>
        <svg viewBox="0 0 16 16" aria-hidden="true"><path d="M3.5 1 6 4 4.6 5.8c.8 2 2.6 3.8 4.6 4.6L11 9l3 2.5-1.4 2.9C7 14.6 1.4 9 1.6 3.4z"/></svg>
        1-888-DULOM-47
      </li>
      <li>
        <svg viewBox="0 0 16 16" aria-hidden="true"><path d="M4 0h8a1 1 0 0 1 1 1v14a1 1 0 0 1-1 1H4a1 1 0 0 1-1-1V1a1 1 0 0 1 1-1zm1 2v10h6V2zm3 11a1 1 0 1 0 0 2 1 1 0 0 0 0-2z" fill-rule="evenodd"/></svg>
        317-555-0193
      </li>
      <li>
        <svg viewBox="0 0 16 16" aria-hidden="true"><path d="M1 3h14v1.2L8 8.6 1 4.2zm0 2.6 7 4.4 7-4.4V13H1z"/></svg>
        info@dulomhome.com
      </li>
    </ul>

    <div class="credentials">
      <p>LICENSED</p>
      <p>INSURED | BONDED</p>
    </div>

    <svg class="footer-band" viewBox="0 0 745 42" aria-hidden="true">
      <polygon points="0,23 431,23 421,42 0,42" fill="var(--brand-red)"/>
      <polygon points="447,0 745,0 745,42 421,42" fill="var(--card-dark)"/>
    </svg>
    <p class="website">www.dulomhome.com</p>
  </section>

  <section class="card card-back" aria-label="Business card back">
    <p class="company-name">Dulom Home Remodeling</p>

    <svg class="social" width="200" height="26" viewBox="0 0 200 26" role="img" aria-label="Social media links">
      <line x1="0" y1="13" x2="56" y2="13" stroke="#8a8a8a" stroke-width="1.5"/>
      <line x1="144" y1="13" x2="200" y2="13" stroke="#8a8a8a" stroke-width="1.5"/>
      <circle cx="70" cy="13" r="12" fill="var(--pale)"/>
      <circle cx="100" cy="13" r="12" fill="var(--pale)"/>
      <circle cx="130" cy="13" r="12" fill="var(--pale)"/>
    </svg>
  </section>

</main>
</body>
</html>
```